UK Online Auction Site needs a clever design

We need a contemporary landing page and registration page design for a UK auction website, that look equally at home on PC's and tablets . The design should be fresh, bright, clean, professional, robust, and familiar. We would like to see something clever but functional.

Online

```html
<!DOCTYPE html>
<html lang="en">
<head>
<meta charset="utf-8">
<title>Bidwell – Online Auctions</title>
<link href="https://fonts.googleapis.com/css2?family=Open+Sans:wght@400;600&family=Roboto+Condensed:wght@400;700&family=Roboto:wght@300;400&display=swap" rel="stylesheet">
<style>
  :root {
    --blue: #0b86d3;
    --blue-dark: #0a6fb0;
    --orange: #f7a20a;
    --green: #3a9a2c;
    --ink: #333333;
    --muted: #555555;
    --page: #f7f7f7;
    --footer: #1e1e1e;
    --footer-text: #cfcfcf;
    --caption: rgba(20,20,20,0.78);
  }
  * { box-sizing: border-box; margin: 0; padding: 0; }
  html, body { width: 880px; height: 1200px; overflow: hidden; }
  body { background: var(--page); font-family: "Open Sans", sans-serif; color: var(--ink); position: relative; }

  .site-header { position: absolute; top: 0; left: 0; width: 880px; height: 86px; background: #fff; }
  .brand { position: absolute; left: 88px; top: 22px; font-family: "Roboto Condensed", sans-serif; font-weight: 700; font-size: 34px; color: var(--blue); display: flex; align-items: center; gap: 8px; }
  .brand-dot { width: 14px; height: 14px; border-radius: 50%; background: var(--blue); }
  .main-nav { position: absolute; left: 365px; top: 35px; display: flex; align-items: center; gap: 14px; font-family: "Roboto Condensed", sans-serif; font-size: 13px; color: var(--ink); }
  .nav-sell { background: var(--blue); color: #fff; padding: 4px 14px; border-radius: 2px; }
  .nav-sep { color: #bbb; }
  .btn-register { position: absolute; left: 717px; top: 35px; width: 75px; height: 22px; background: var(--green); color: #fff; font-family: "Roboto Condensed", sans-serif; font-size: 12px; display: flex; align-items: center; justify-content: center; border-radius: 2px; }

  .search-bar { position: absolute; top: 86px; left: 0; width: 880px; height: 39px; background: var(--blue); border-top: 3px solid var(--blue-dark); }
  .search-cat { position: absolute; left: 123px; top: 5px; width: 152px; height: 28px; background: #fff; font-family: "Roboto Condensed", sans-serif; font-size: 10px; color: var(--ink); padding: 8px 14px; border-right: 1px solid #ddd; }
  .search-cat::after { content: "▾"; position: absolute; right: 12px; top: 8px; font-size: 9px; }
  .search-input { position: absolute; left: 275px; top: 5px; width: 351px; height: 28px; background: #fff; font-family: "Roboto Condensed", sans-serif; font-size: 10px; color: var(--muted); padding: 8px 14px; }
  .search-btn { position: absolute; left: 640px; top: 4px; width: 119px; height: 30px; background: var(--orange); color: #fff; font-family: "Roboto Condensed", sans-serif; font-size: 16px; display: flex; align-items: center; justify-content: center; gap: 6px; border-radius: 2px; }

  .hero { position: absolute; top: 125px; left: 0; width: 880px; height: 345px; overflow: hidden; }
  .hero-photo { position: absolute; inset: 0; background:
      radial-gradient(ellipse 240px 260px at 660px 170px, #b98a70 0%, #6b4330 45%, rgba(0,0,0,0) 75%),
      radial-gradient(ellipse 220px 160px at 120px 300px, rgba(120,50,150,0.7) 0%, rgba(0,0,0,0) 70%),
      linear-gradient(90deg, #0a0a10 0%, #1a0f22 45%, #2a1a18 100%); }
  .hero-text { position: absolute; left: 88px; top: 72px; color: #fff; }
  .hero-kicker { font-family: "Roboto", sans-serif; font-weight: 300; font-size: 35px; letter-spacing: 0.5px; }
  .hero-offer { font-family: "Roboto", sans-serif; font-weight: 300; font-size: 78px; line-height: 1; margin-top: 2px; }
  .hero-offer .pct { color: var(--orange); }
  .hero-sub { font-family: "Open Sans", sans-serif; font-size: 21px; margin-top: 6px; }
  .btn-shop { position: absolute; left: 88px; top: 240px; width: 126px; height: 33px; background: var(--blue); border-bottom: 3px solid var(--blue-dark); color: #fff; font-size: 15px; display: flex; align-items: center; justify-content: center; gap: 6px; }

  .top-products { position: absolute; top: 500px; left: 0; width: 880px; text-align: center; }
  .section-title { font-family: "Roboto Condensed", sans-serif; font-weight: 700; font-size: 25px; color: var(--blue); }
  .section-lede { font-size: 12px; color: var(--muted); margin-top: 6px; }

  .tile { position: absolute; width: 166px; height: 214px; overflow: hidden; border: 1px solid #e2e2e2; }
  .tile-photo { position: absolute; inset: 0; }
  .tile-caption { position: absolute; left: 0; bottom: 0; width: 100%; height: 46px; background: var(--caption); color: #fff; text-align: center; padding-top: 6px; }
  .tile-name { font-size: 13px; font-weight: 600; }
  .tile-link { font-size: 8px; margin-top: 1px; }
  .tile-feature { background: linear-gradient(160deg, #1d9be0, #0b78c2); color: #fff; text-align: center; padding-top: 38px; }
  .tile-feature .feature-brand { font-family: "Open Sans", sans-serif; font-weight: 600; font-size: 20px; }
  .tile-feature .tile-name { margin-top: 6px; }
  .tile-feature p { font-size: 8.5px; font-weight: 600; line-height: 1.25; margin: 6px 12px 0; }
  .tile-feature .feature-link { display: inline-block; border: 1px solid #fff; font-size: 8px; padding: 4px 10px; margin-top: 10px; }

  .site-footer { position: absolute; top: 1049px; left: 0; width: 880px; height: 151px; background: var(--footer); color: var(--footer-text); font-size: 9px; }
  .footer-col { position: absolute; top: 26px; }
  .footer-col h4 { font-family: "Roboto Condensed", sans-serif; font-weight: 400; font-size: 12px; color: #fff; margin-bottom: 10px; }
  .footer-col ul { list-style: none; }
  .footer-col li { margin-bottom: 7px; }
  .social li { display: flex; align-items: center; gap: 10px; margin-bottom: 6px; }
  .social-mark { width: 20px; height: 20px; border-radius: 2px; }
  .footer-brand { position: absolute; left: 672px; top: 28px; font-weight: 600; font-size: 30px; color: #555; }
  .copyright { position: absolute; right: 89px; top: 92px; text-align: right; font-size: 9.5px; line-height: 1.35; }
</style>
</head>
<body>

<header class="site-header">
  <div class="brand"><span class="brand-dot"></span>Bidwell</div>
  <nav class="main-nav">
    <span class="nav-sell">Sell ▾</span>
    <span>👤 Sign Up ▾</span>
    <span>Basket ▾</span><span class="nav-sep">|</span>
    <span>? Help</span><span class="nav-sep">|</span>
    <span>✉ Contact</span>
  </nav>
  <div class="btn-register">Register</div>
</header>

<div class="search-bar">
  <div class="search-cat">All Categories</div>
  <div class="search-input">Search for a brand,product or specific item</div>
  <div class="search-btn">
    <svg width="14" height="14" viewBox="0 0 14 14"><circle cx="5.5" cy="5.5" r="4.2" fill="none" stroke="#fff" stroke-width="2"/><line x1="8.6" y1="8.6" x2="13" y2="13" stroke="#fff" stroke-width="2.4"/></svg>
    Search
  </div>
</div>

<section class="hero">
  <div class="hero-photo" role="img" aria-label="Close-up beauty portrait of a woman with bokeh lights on a dark background"></div>
  <div class="hero-text">
    <div class="hero-kicker">JEWELLERY &amp; BEAUTY</div>
    <div class="hero-offer"><span class="pct">25%</span> OFF</div>
    <div class="hero-sub">ONLINE &amp; IN STORE</div>
  </div>
  <div class="btn-shop">
    <svg width="12" height="11" viewBox="0 0 12 11"><path d="M1 4h10l-1.4 6.5H2.4z" fill="#fff"/><path d="M3 4l3-3 3 3" fill="none" stroke="#fff" stroke-width="1.2"/></svg>
    Shop Now
  </div>
</section>

<section class="top-products">
  <h2 class="section-title">Top Products</h2>
  <p class="section-lede">It is a long established fact that a reader will be distracted by the readable content.</p>
</section>

<article class="tile" style="left:88px;top:580px">
  <div class="tile-photo" role="img" aria-label="Fashion model in sunglasses and patterned scarf" style="background:linear-gradient(180deg,#4a3a38,#b03a35 55%,#2a2222)"></div>
  <div class="tile-caption"><div class="tile-name">Fashion</div><div class="tile-link">See All Product →</div></div>
</article>
<article class="tile" style="left:268px;top:580px">
  <div class="tile-photo" role="img" aria-label="House with garden and trees" style="background:linear-gradient(180deg,#5c7a3a,#8a8478 50%,#4f6b35)"></div>
  <div class="tile-caption"><div class="tile-name">Home &amp; Garden</div><div class="tile-link">See All Product →</div></div>
</article>
<article class="tile tile-feature" style="left:448px;top:580px">
  <div class="feature-brand">Bidwell</div>
  <div class="tile-name">Electricals &amp; Technology</div>
  <p>It is a long established fact that a reader will be distracted by the readable content</p>
  <span class="feature-link">See All Product →</span>
</article>
<article class="tile" style="left:626px;top:580px">
  <div class="tile-photo" role="img" aria-label="Elegant bright room with chandelier and antiques" style="background:linear-gradient(180deg,#e8e4dc,#c9c0b2 60%,#8a7d6c)"></div>
  <div class="tile-caption"><div class="tile-name">Collectables &amp; Aniques</div><div class="tile-link">See All Product →</div></div>
</article>

<article class="tile" style="left:88px;top:808px">
  <div class="tile-photo" role="img" aria-label="Woman wearing jewellery necklace and earrings" style="background:linear-gradient(180deg,#bfb5b3,#c89e88 50%,#8d7a76)"></div>
  <div class="tile-caption"><div class="tile-name">Jewellery &amp; Beauty</div><div class="tile-link">See All Product →</div></div>
</article>
<article class="tile" style="left:268px;top:808px">
  <div class="tile-photo" role="img" aria-label="White teddy bear with checked bow" style="background:linear-gradient(180deg,#e6d8b0,#efe8dc 50%,#c9b890)"></div>
  <div class="tile-caption"><div class="tile-name">Toy</div><div class="tile-link">See All Product →</div></div>
</article>
<article class="tile" style="left:448px;top:808px">
  <div class="tile-photo" role="img" aria-label="Bowling balls in front of bowling pins" style="background:linear-gradient(180deg,#3a8bb5,#5a5a5a 45%,#1f5a6a 70%,#c24a20)"></div>
  <div class="tile-caption"><div class="tile-name">Sport &amp; Leisure</div><div class="tile-link">See All Product →</div></div>
</article>
<article class="tile" style="left:626px;top:808px">
  <div class="tile-photo" role="img" aria-label="Black racing motorbike" style="background:linear-gradient(180deg,#8a8e92,#2a2a2a 55%,#151515)"></div>
  <div class="tile-caption"><div class="tile-name">Motors</div><div class="tile-link">See All Product →</div></div>
</article>

<footer class="site-footer">
  <div class="footer-col" style="left:89px"><h4>Site Map</h4>
    <ul><li>Contact</li><li>Terms</li><li>Privacy</li><li>RSS</li></ul></div>
  <div class="footer-col" style="left:158px;top:50px"><ul><li>About</li><li>News</li><li>Feeds</li></ul></div>
  <div class="footer-col" style="left:261px"><h4>Buy</h4>
    <ul><li>Categories</li><li>Search</li><li>Currency</li><li>Converter</li></ul></div>
  <div class="footer-col" style="left:377px"><h4>Sell</h4>
    <ul><li>Sell New Item</li><li>Sell Bulk Items</li></ul></div>
  <div class="footer-col social" style="left:517px;top:21px"><h4>Follow Us</h4>
    <ul>
      <li><span class="social-mark" style="background:#3b5b9a"></span>Social Page</li>
      <li><span class="social-mark" style="background:#2aa3dd"></span>Microblog</li>
      <li><span class="social-mark" style="background:#d23c2c"></span>Circles</li>
    </ul></div>
  <div class="footer-brand">Bidwell</div>
  <div class="copyright">Copyright Bidwell ® 2003-13. All<br>rights reserved</div>
</footer>

</body>
</html>
```